Lumbra Ember Oven Kitchen (restaurant)

Restaurant with a cool vibe.
We need a refresh of existing site. Appealing to a hip crowd of 25 or older age bracket (mid price to high small town). Constant changes food and cocktail menu. A vibing atmosphere with jazz funk hip music.
Must be able to scale for any device… phone/mobile device super important.
Instagram: @Lumbra.Bexwell
Website: lumbrabexwell.example

Target Market(s)

25-55 age group

Number of Pages Required

1 page

Font styles to use
Sans Serif

Requirements
Must have
• Simple to navigate. Simplicity is the key to all sophistication.

Links/Buttons
Menu
Gift Cards
Reservations
Take Out
Contact Us
Should not have
• Please, nothing generic looking… no cookie cutter look. Originality

```html
<!DOCTYPE html>
<html lang="en">
<head>
<meta charset="utf-8">
<title>Lumbra Ember Oven Kitchen</title>
<link rel="stylesheet" href="https://fonts.googleapis.com/css2?family=Poppins:wght@400;500;600&family=Roboto+Condensed:wght@700&family=Rakkas&family=Noto+Serif:wght@700&display=swap">
<style>
:root{
  --yellow:#ffcb32;
  --yellow-deep:#f6bd1c;
  --orange:#d0680c;
  --ink:#1e1e1e;
  --dark:#232323;
  --text:#444;
  --muted:#666;
  --white:#fff;
}
*{box-sizing:border-box;margin:0;padding:0}
html,body{width:1200px;height:4060px;overflow:hidden}
body{position:relative;font-family:"Poppins",sans-serif;color:var(--text);background:var(--white)}
.abs{position:absolute}
.ph{position:absolute}
.cond{font-family:"Roboto Condensed",sans-serif;font-weight:700;text-transform:uppercase;color:var(--ink)}
.btn{position:absolute;display:flex;align-items:center;justify-content:center;font-family:"Noto Serif",serif;font-weight:700;font-size:15px;letter-spacing:.5px;color:var(--ink);background:var(--yellow)}

/* hero */
.hero{position:absolute;left:0;top:0;width:1200px;height:653px;background:radial-gradient(ellipse at 30% 40%,#5a5a3c 0%,#2f2d24 45%,#1a1a16 100%)}
.hero-shade{position:absolute;inset:0;background:rgba(0,0,0,.35)}
.topbar{position:absolute;left:0;top:0;width:1200px;height:40px;font-size:12px;color:var(--white)}
.topbar span{position:absolute;top:12px;display:flex;align-items:center;gap:10px}
.nav{position:absolute;left:60px;top:40px;width:1080px;height:60px;background:rgba(20,20,20,.55);font-size:12px;color:var(--white)}
.nav a{position:absolute;top:23px;color:var(--white);text-decoration:none}
.nav a.active{color:var(--yellow)}
.brand{position:absolute;left:50%;top:12px;transform:translateX(-50%);font-family:"Poppins",sans-serif;font-weight:600;font-size:26px;letter-spacing:2px;color:var(--white)}
.hero-kicker{position:absolute;top:247px;width:100%;text-align:center;font-size:21px;color:var(--yellow)}
.hero-title{position:absolute;top:282px;width:100%;text-align:center;font-family:"Rakkas",serif;font-size:70px;line-height:76px;color:var(--white)}
.btn-ghost{background:transparent;border:1px solid var(--yellow);color:var(--white)}

/* menu */
.section-title{position:absolute;width:100%;text-align:center;font-size:31px}
.tabs{position:absolute;left:184px;top:803px;height:34px;font-size:13px;color:var(--ink)}
.tabs span{position:absolute;top:8px;white-space:nowrap}
.tabs .on{top:0;height:34px;padding:8px 22px;background:var(--yellow)}
.menu-frame{position:absolute;left:150px;top:837px;width:900px;height:625px;border:2px solid var(--yellow)}
.menu-inner{position:absolute;left:6px;top:6px;right:6px;bottom:6px;border:1px solid #eee;background:#f7f7f7}
.item{position:absolute;width:390px}
.item h3{font-weight:500;font-size:17px;color:var(--ink);padding-bottom:6px;border-bottom:1px dotted #999;width:300px}
.item p{font-size:12px;line-height:19px;color:var(--muted);margin-top:6px;width:385px}
.price{position:absolute;right:0;top:-10px;width:46px;height:46px;border-radius:50%;background:var(--orange);color:var(--white);font-size:18px;display:flex;align-items:center;justify-content:center;box-shadow:0 0 0 2px #f7f7f7,0 0 0 3px var(--orange)}
.item.featured{left:188px;top:1071px;width:366px;height:107px;background:var(--yellow);border-radius:4px;padding:18px 24px 0}
.item.featured .price{right:16px;top:10px;background:var(--yellow);color:#c62a00;box-shadow:0 0 0 2px var(--ink)}
.item.featured h3{border-bottom-color:#9a6f00}
.item.featured p{color:#7a5200;width:300px}

/* gift band */
.gift{position:absolute;left:0;top:1558px;width:1200px;height:443px;background:var(--yellow)}
.gift-title{position:absolute;left:864px;top:124px;font-size:29px;line-height:36px}
.gift-sub{position:absolute;left:864px;top:223px;font-size:14px;color:var(--ink)}
.gift-tag{position:absolute;left:864px;top:254px;font-family:"Rakkas",serif;font-size:22px;color:var(--white)}
.gift-phone{position:absolute;left:860px;top:312px;display:flex;align-items:center;gap:16px;font-size:23px;font-weight:500;color:var(--ink)}
.badge{position:absolute;left:212px;top:117px;width:112px;height:112px;border-radius:50%;background:var(--orange);color:var(--white);text-align:center;font-size:17px;line-height:28px;padding-top:28px}
.badge em{font-style:normal;color:var(--yellow)}
.gift-word{position:absolute;left:52px;top:90px;transform:rotate(-42deg);transform-origin:left top;font-family:"Poppins",sans-serif;font-weight:600;font-size:62px;color:var(--ink);letter-spacing:2px;top:220px}

/* contact */
.contact-title{position:absolute;left:60px;top:2095px;font-size:31px}
.hours{position:absolute;top:2150px;font-size:12px;color:var(--ink)}
.hours h4{font-weight:400;font-size:20px;color:var(--orange);margin-bottom:14px;white-space:nowrap}
.hours li{list-style:none;height:39px}
.thumb{position:absolute;top:2380px;width:150px;height:150px}

/* reservation */
.reserve{position:absolute;left:0;top:2654px;width:600px;height:449px;background:var(--dark)}
.reserve-title{position:absolute;left:60px;top:82px;font-size:31px;color:var(--white)}
.field{position:absolute;height:36px;background:#333;color:#ddd;font-size:12px;display:flex;align-items:center;padding-left:38px}
.field svg{position:absolute;left:12px;top:12px}
.field .caret{position:absolute;right:14px;top:16px;border:4px solid transparent;border-top-color:#bbb}

/* specialty */
.special{position:absolute;left:0;top:3103px;width:1200px;height:513px;background:linear-gradient(90deg,#fff 0%,#fbf8f1 60%,#f3ead9 100%)}
.special-title{position:absolute;left:512px;top:127px;font-size:31px}
.special-sub{position:absolute;left:512px;top:173px;font-size:25px;color:var(--orange)}
.special-body{position:absolute;left:512px;top:236px;width:360px;font-size:12px;line-height:20px;color:var(--muted)}

/* footer */
.footer{position:absolute;left:0;top:3616px;width:1200px;height:444px;background:linear-gradient(180deg,#2a2622,#15130f)}
.foot-brand{position:absolute;left:60px;top:82px;font-weight:600;font-size:38px;letter-spacing:2px;color:var(--white)}
.foot-text{position:absolute;left:60px;top:171px;width:470px;font-size:12px;line-height:20px;color:#ddd}
.foot-contact{position:absolute;top:256px;display:flex;align-items:center;gap:14px;font-size:12px;color:var(--white)}
.ring{width:36px;height:36px;border-radius:50%;border:2px solid var(--yellow);display:flex;align-items:center;justify-content:center}
.copy{position:absolute;left:0;top:4036px;width:1200px;text-align:center;font-size:11px;color:#ddd}
.hours-card{position:absolute;left:793px;top:3588px;width:346px;height:362px;background:var(--yellow)}
.hours-card .inner{position:absolute;inset:14px;border:1px solid var(--white)}
.hours-card h4{position:absolute;left:38px;top:58px;font-size:22px}
.hours-card ul{position:absolute;left:38px;top:108px;font-size:11px;color:var(--ink);list-style:none}
.hours-card li{height:39px}
.hours-card .res{position:absolute;left:0;width:100%;text-align:center;top:272px;font-family:"Roboto Condensed",sans-serif;font-weight:700;font-size:19px;color:var(--white)}
.hours-card .num{position:absolute;left:0;width:100%;text-align:center;top:302px;font-size:23px;font-weight:500;color:var(--ink)}
</style>
</head>
<body>

<!-- Hero -->
<header class="hero">
  <div class="ph" role="img" aria-label="Overhead photo of bowls of green dip and hummus on a dark woven table" style="inset:0;background:radial-gradient(circle at 22% 45%,#6b6a42 0%,#3a3828 30%,transparent 55%),radial-gradient(circle at 72% 55%,#5d5c3c 0%,#34321f 28%,transparent 52%)"></div>
  <div class="hero-shade"></div>
  <div class="topbar">
    <span style="left:60px"><svg width="16" height="16" viewBox="0 0 24 24"><path fill="#ffcb32" d="M6.6 10.8a15 15 0 0 0 6.6 6.6l2.2-2.2c.3-.3.7-.4 1-.2 1.1.4 2.3.6 3.6.6.6 0 1 .4 1 1V20c0 .6-.4 1-1 1A17 17 0 0 1 3 4c0-.6.4-1 1-1h3.5c.6 0 1 .4 1 1 0 1.3.2 2.5.6 3.6.1.3 0 .7-.2 1z"/></svg>555-014-0283</span>
    <span style="left:262px"><svg width="20" height="14" viewBox="0 0 20 14"><rect width="20" height="14" fill="#ffcb32"/><path d="M0 0l10 8 10-8" fill="none" stroke="#2a2a2a" stroke-width="1.5"/></svg>hello@lumbrabexwell.example</span>
    <span style="right:60px"><svg width="14" height="18" viewBox="0 0 14 18"><path fill="#ffcb32" d="M7 0a7 7 0 0 0-7 7c0 5 7 11 7 11s7-6 7-11a7 7 0 0 0-7-7zm0 9.5A2.5 2.5 0 1 1 7 4.5a2.5 2.5 0 0 1 0 5z"/></svg>48 Marlow Street Bexwell, ON</span>
  </div>
  <nav class="nav">
    <a class="active" style="left:46px">Home</a>
    <a style="left:113px">Area For Gift Cards</a>
    <a style="left:263px">Menu</a>
    <div class="brand">LUMBRA</div>
    <a style="left:770px">Contact Us</a>
    <a style="left:871px">Reservations</a>
    <a style="left:980px">Take Out</a>
  </nav>
  <div class="hero-kicker">Ember Oven Kitchen</div>
  <h1 class="hero-title">Lets Get Lunch At<br>Lumbra!</h1>
  <a class="btn" style="left:443px;top:481px;width:150px;height:36px">ORDER NOW</a>
  <a class="btn btn-ghost" style="left:608px;top:481px;width:150px;height:36px">BOOK A TABLE</a>
</header>

<!-- Menu -->
<section>
  <h2 class="section-title cond" style="top:730px">Our Menu</h2>
  <div class="tabs">
    <span class="on" style="left:0">Shareables</span>
    <span style="left:174px">Wood Fired Pizza</span>
    <span style="left:346px">Salad</span>
    <span style="left:440px">Sandwiches</span>
    <span style="left:575px">Burgers</span>
    <span style="left:684px">Mains &amp; Pasta</span>
  </div>
  <div class="ph" role="img" aria-label="Gold dinner fork" style="left:74px;top:858px;width:34px;height:610px;background:linear-gradient(90deg,#b78a3c,#f0d58e,#a37425);border-radius:16px 16px 8px 8px"></div>
  <div class="ph" role="img" aria-label="Gold dinner knife" style="left:1092px;top:866px;width:34px;height:598px;background:linear-gradient(90deg,#a37425,#f0d58e,#b78a3c);border-radius:18px 6px 8px 8px"></div>
  <div class="menu-frame"><div class="menu-inner"></div></div>
  <div class="ph" role="img" aria-label="Platter of loaded nachos with salsa and lime" style="left:170px;top:883px;width:382px;height:166px;background:radial-gradient(ellipse at 50% 55%,#e6c37a 0%,#cf9a4a 45%,#eee 72%,transparent 74%)"></div>

  <div class="item featured"><h3>Wood Fired Brussels Sprouts</h3><p>Smoked bacon, parmesan, fresh lemon, cherry tomato, garlic aioli</p><span class="price">$10</span></div>
  <div class="item" style="left:212px;top:1212px"><h3>Pita Dip Duo</h3><p>House-made spicy red pepper feta dip, roasted garlic &amp; spinach hummus, grilled pita bread</p><span class="price" style="right:0">$20</span></div>
  <div class="item" style="left:212px;top:1318px"><h3>Argentinian Chicken Tacos</h3><p>Argentinian grilled chicken, charred sweet corn, red cabbage, handmade guacamole and house chimichurri</p><span class="price">$15</span></div>

  <div class="item" style="left:638px;top:890px"><h3>Pork Belly Tacos</h3><p>Slow roasted, crispy pork belly, sweet sesame sriracha sauce, julienne carrots, bean sprouts, house kimchi</p><span class="price">$18</span></div>
  <div class="item" style="left:638px;top:988px"><h3>Butternut &amp; Sausage Skewers</h3><p>Roasted butternut squash, grilled sausage, herbed ricotta, fresh arugula &amp; cherry tomato</p><span class="price">$16</span></div>
  <div class="item" style="left:638px;top:1093px"><h3>Magnolia Flatbread</h3><p>Balsamic onion jam, smoked bacon, goat cheese, fresh arugula &amp; balsamic drizzle</p><span class="price">$20</span></div>
  <div class="item" style="left:638px;top:1212px"><h3>Wood Fired Green Beans</h3><p>Wood-oven green beans, fresh lemon, cherry tomato, shaved parmesan, sriracha aioli</p><span class="price">$14</span></div>
  <div class="item" style="left:638px;top:1325px"><h3>Wood Fired Wings</h3><p>Whole chicken wings, baked in our wood burning oven</p><span class="price">$14</span></div>
</section>

<!-- Gift card band -->
<section class="gift">
  <svg class="abs" style="left:0;top:0" width="1200" height="443" viewBox="0 0 1200 443">
    <polygon points="0,0 426,0 0,382" fill="#f8c02a"/>
    <polygon points="410,0 440,0 0,400 0,372" fill="#c4780c"/>
    <polygon points="880,0 920,0 708,443 668,443" fill="#c4780c"/>
  </svg>
  <svg class="abs" style="left:0;top:0" width="1200" height="443" viewBox="0 0 1200 443" role="img" aria-label="Close-up of grilled chicken with rice and greens">
    <defs><linearGradient id="grill" x1="0" y1="0" x2="1" y2="1"><stop offset="0" stop-color="#4a3a28"/><stop offset=".45" stop-color="#b9a892"/><stop offset=".7" stop-color="#5b4a36"/><stop offset="1" stop-color="#2e3a26"/></linearGradient></defs>
    <polygon points="440,0 880,0 668,443 0,443 0,400" fill="url(#grill)"/>
  </svg>
  <div class="gift-word">LUMBRA</div>
  <div class="badge">Special<br><em>Gift Card</em></div>
  <h2 class="gift-title cond">Area For Gift<br>Card</h2>
  <div class="gift-sub">Ember Oven Kitchen</div>
  <div class="gift-tag">Lets Get Lunch At Lumbra!</div>
  <div class="gift-phone"><span class="ring" style="width:50px;height:50px;border-color:var(--ink)"><svg width="22" height="22" viewBox="0 0 24 24"><path fill="#1e1e1e" d="M6.6 10.8a15 15 0 0 0 6.6 6.6l2.2-2.2c.3-.3.7-.4 1-.2 1.1.4 2.3.6 3.6.6.6 0 1 .4 1 1V20c0 .6-.4 1-1 1A17 17 0 0 1 3 4c0-.6.4-1 1-1h3.5c.6 0 1 .4 1 1 0 1.3.2 2.5.6 3.6.1.3 0 .7-.2 1z"/></svg></span>555-014-0283</div>
</section>

<!-- Contact -->
<section>
  <h2 class="contact-title cond">Contact Us</h2>
  <div class="hours" style="left:60px"><h4>Canada Day Hours!</h4><ul><li>Thursday, July 1st &nbsp;- &nbsp;Open</li><li>Friday, July 2nd &nbsp;- &nbsp;Open</li><li>Saturday, July 3rd &nbsp;- &nbsp;Open</li><li>Sunday, July 4th &nbsp;- &nbsp;Closed</li></ul></div>
  <div class="hours" style="left:301px"><h4>Takeout &amp; Kitchen Hours</h4><ul><li>Thursday to Sunday</li><li>12:00pm - 8:00pm</li></ul></div>
  <div class="hours" style="left:587px"><h4>Outdoor Dining Hours</h4><ul><li>Our courtyard is open!</li><li>Thursday to Sunday</li><li>12:00pm - 9:00pm</li></ul></div>
  <div class="ph" role="img" aria-label="Two wood fired pizzas and a cocktail on a patterned table" style="left:836px;top:2091px;width:304px;height:451px;background:radial-gradient(circle at 40% 70%,#d9693f 0%,#c75a33 30%,#6a5a78 62%,#3c3550 100%)"></div>
  <div class="thumb" role="img" aria-label="Plated salad with grilled chicken" style="left:60px;background:radial-gradient(circle,#c9b48a,#7c7060)"></div>
  <div class="thumb" role="img" aria-label="Dining room interior at night" style="left:240px;background:linear-gradient(#5a3e3e,#2a1f24)"></div>
  <div class="thumb" role="img" aria-label="Restaurant team gathered together" style="left:420px;background:linear-gradient(#4a3a34,#1f1a18)"></div>
  <div class="thumb" role="img" aria-label="Plated dish on a dark table" style="left:600px;background:radial-gradient(circle,#7a7466,#3a3832)"></div>
  <div class="thumb" role="img" aria-label="Tacos with red cabbage" style="left:780px;background:radial-gradient(circle,#8a7c62,#3d4030)"></div>
</section>

<!-- Reservation -->
<section>
  <div class="reserve">
    <h2 class="reserve-title cond">Make A Reservation</h2>
    <div class="field" style="left:60px;top:140px;width:244px"><svg width="14" height="11" viewBox="0 0 14 11"><rect x=".5" y=".5" width="13" height="10" fill="none" stroke="#999"/><path d="M.5.5l6.5 5 6.5-5" fill="none" stroke="#999"/></svg>Email</div>
    <div class="field" style="left:322px;top:140px;width:243px"><svg width="10" height="13" viewBox="0 0 10 13"><circle cx="5" cy="3" r="2.5" fill="#999"/><rect x="2" y="6" width="6" height="7" fill="#999"/></svg>Person<span class="caret"></span></div>
    <div class="field" style="left:60px;top:199px;width:244px"><svg width="12" height="12" viewBox="0 0 12 12"><rect x=".5" y="1.5" width="11" height="10" fill="none" stroke="#999"/><rect x=".5" y="1.5" width="11" height="3" fill="#999"/></svg>Date</div>
    <div class="field" style="left:322px;top:199px;width:243px"><svg width="12" height="12" viewBox="0 0 12 12"><circle cx="6" cy="6" r="5.5" fill="none" stroke="#999"/><path d="M6 3v3h2.5" fill="none" stroke="#999"/></svg>7:00 Am<span class="caret"></span></div>
    <div class="field" style="left:60px;top:252px;width:505px;height:67px"></div>
    <a class="btn" style="left:60px;top:334px;width:150px;height:37px">BOOK TABLE</a>
  </div>
  <div class="ph" role="img" aria-label="Cozy dining room with brick wall, wooden tables and big windows" style="left:600px;top:2654px;width:600px;height:449px;background:linear-gradient(100deg,#c8d2d4 0%,#8d7a62 35%,#a0573a 60%,#6b3b24 100%)"></div>
</section>

<!-- Specialty -->
<section class="special">
  <div class="ph" role="img" aria-label="Mushroom and herb pizza on a white plate" style="left:0;top:35px;width:315px;height:402px;background:radial-gradient(ellipse at 45% 50%,#c98a4c 0%,#a8603a 45%,#e9e4dc 68%,transparent 71%)"></div>
  <h2 class="special-title cond">Our Specialty Cuisine</h2>
  <div class="special-sub">Special Promotion This Month !</div>
  <p class="special-body">Reservations will not be available for the courtyard Under phase 1 and 2 of reopening. Walk-ins only. We can't wait to see you!</p>
  <a class="btn" style="left:512px;top:320px;width:133px;height:34px">TAKE OUT</a>
</section>

<!-- Footer -->
<footer class="footer" role="contentinfo">
  <div class="ph" role="img" aria-label="Dim brick building facade at night" style="inset:0;background:linear-gradient(90deg,rgba(70,50,40,.35),rgba(0,0,0,0))"></div>
  <div class="foot-brand">LUMBRA</div>
  <p class="foot-text">Reservations will not be available for the courtyard Under phase 1 and 2 of reopening. Walk-ins only. We can't wait to see you!</p>
  <div class="foot-contact" style="left:58px"><span class="ring"><svg width="12" height="16" viewBox="0 0 14 18"><path fill="#ffcb32" d="M7 0a7 7 0 0 0-7 7c0 5 7 11 7 11s7-6 7-11a7 7 0 0 0-7-7zm0 9.5A2.5 2.5 0 1 1 7 4.5a2.5 2.5 0 0 1 0 5z"/></svg></span>48 Marlow Street Bexwell, ON</div>
  <div class="foot-contact" style="left:352px"><span class="ring"><svg width="16" height="16" viewBox="0 0 24 24"><path fill="#ffcb32" d="M6.6 10.8a15 15 0 0 0 6.6 6.6l2.2-2.2c.3-.3.7-.4 1-.2 1.1.4 2.3.6 3.6.6.6 0 1 .4 1 1V20c0 .6-.4 1-1 1A17 17 0 0 1 3 4c0-.6.4-1 1-1h3.5c.6 0 1 .4 1 1 0 1.3.2 2.5.6 3.6.1.3 0 .7-.2 1z"/></svg></span>555-014-0283</div>
  <div class="foot-contact" style="left:545px"><span class="ring"><svg width="16" height="11" viewBox="0 0 20 14"><rect width="20" height="14" fill="#ffcb32"/><path d="M0 0l10 8 10-8" fill="none" stroke="#2a2a2a" stroke-width="1.5"/></svg></span>hello@lumbrabexwell.example</div>
</footer>
<div class="hours-card">
  <div class="inner"></div>
  <h4 class="cond">Canada Day Hours !</h4>
  <ul>
    <li>Thursday, July 1st ............... Open</li>
    <li>Friday, July 2nd ............... Open</li>
    <li>Saturday, July 3rd ............... Open</li>
    <li>Sunday, July 4th ............... Closed</li>
  </ul>
  <div class="res">RESERVATION NUMBER</div>
  <div class="num">555-014-0283</div>
</div>
<div class="copy">© 2021 LUMBRA . All Rights Reserved.</div>

</body>
</html>
```